Veldmark Supplies Business Card

Professional business card that stand out to our potential customers. Front and back with clean modern design

Industry/Entity Type

Oil and gas

Contact Information for Business Card

Name, address, website , office phone and cell number

Requirements
Must have
• Editable files for each employee

```html
<!DOCTYPE html>
<html lang="en">
<head>
<meta charset="utf-8">
<title>Veldmark Supplies Business Card</title>
<link rel="stylesheet" href="https://fonts.googleapis.com/css2?family=Poppins:wght@400;600;700&display=swap">
<style>
  :root {
    --page: #e6e7e9;
    --card: #ffffff;
    --card-shade: #eeeeee;
    --red: #e31e2d;
    --blue: #1aa9cf;
    --ink: #3a3a3a;
    --muted: #5a5a5a;
    --rule: #444444;
  }
  * { box-sizing: border-box; margin: 0; padding: 0; }
  html, body { width: 1200px; height: 900px; overflow: hidden; }
  body {
    background: var(--page);
    font-family: "Poppins", sans-serif;
    color: var(--ink);
    position: relative;
  }
  .card {
    position: absolute;
    left: 250px;
    width: 700px;
    height: 400px;
    border-radius: 30px;
    background: linear-gradient(135deg, var(--card) 0%, var(--card) 55%, var(--card-shade) 100%);
    box-shadow: 0 8px 24px rgba(0,0,0,0.18);
    overflow: hidden;
  }
  .card--front { top: 40px; }
  .card--back { top: 470px; }

  .front-mark {
    position: absolute;
    inset: 0;
    display: flex;
    align-items: center;
    justify-content: center;
    gap: 14px;
  }
  .mark-square {
    width: 26px; height: 26px;
    background: var(--red);
  }
  .brand-name {
    font-weight: 700;
    font-size: 34px;
    letter-spacing: 1px;
    text-transform: uppercase;
    color: var(--red);
  }

  .holder {
    position: absolute;
    left: 40px; top: 40px;
  }
  .holder-line {
    font-size: 19px;
    line-height: 1.2;
  }
  .holder-first { font-weight: 700; color: var(--red); }
  .holder-last { font-weight: 700; color: var(--blue); }
  .holder-divider { font-weight: 700; color: var(--blue); margin: 0 4px; }
  .holder-role { color: var(--muted); font-weight: 400; }
  .holder-cell {
    margin-top: 8px;
    display: flex; align-items: center; gap: 10px;
    font-size: 17px; color: var(--muted);
  }

  .contact {
    position: absolute;
    left: 330px; top: 120px;
    list-style: none;
    width: 340px;
  }
  .contact-item {
    display: flex; align-items: center; gap: 10px;
    font-size: 14.5px; color: var(--muted);
    line-height: 30px;
    white-space: nowrap;
  }
  .icon { width: 16px; height: 16px; flex: none; }
  .contact-rule {
    position: absolute;
    left: 330px; top: 262px;
    width: 340px; height: 1.5px;
    background: var(--rule);
  }
  .back-brand {
    position: absolute;
    right: 30px; top: 290px;
    display: flex; align-items: center; gap: 12px;
  }
  .back-brand .brand-name { font-size: 30px; }
  .back-brand .mark-square { width: 22px; height: 22px; }
</style>
</head>
<body>

<section class="card card--front" aria-label="Card front">
  <div class="front-mark">
    <span class="mark-square"></span>
    <span class="brand-name">Veldmark Supplies</span>
  </div>
</section>

<section class="card card--back" aria-label="Card back">
  <div class="holder">
    <p class="holder-line">
      <span class="holder-first">DALE</span>
      <span class="holder-last">MORROW</span><span class="holder-divider">|</span><span class="holder-role">Director</span>
    </p>
    <p class="holder-cell">
      <svg class="icon" viewBox="0 0 16 16" aria-hidden="true"><rect x="4" y="1" width="8" height="14" rx="1.5" fill="none" stroke="var(--red)" stroke-width="1.5"/><line x1="7" y1="12.5" x2="9" y2="12.5" stroke="var(--red)" stroke-width="1.2"/></svg>
      555-200-9000
    </p>
  </div>

  <ul class="contact">
    <li class="contact-item">
      <svg class="icon" viewBox="0 0 16 16" aria-hidden="true"><path d="M3 1.5l3 3-1.5 2a9 9 0 0 0 5 5l2-1.5 3 3-2 2C6 14.5 1.5 10 1 3z" fill="var(--red)"/></svg>
      (555)610-0624
    </li>
    <li class="contact-item">
      <svg class="icon" viewBox="0 0 16 16" aria-hidden="true"><rect x="1" y="3" width="14" height="10" fill="var(--red)"/><path d="M1 3l7 6 7-6" fill="none" stroke="#fff" stroke-width="1.3"/></svg>
      sales@veldmarksupplies.com
    </li>
    <li class="contact-item">
      <svg class="icon" viewBox="0 0 16 16" aria-hidden="true"><circle cx="8" cy="8" r="6.5" fill="none" stroke="var(--red)" stroke-width="1.3"/><ellipse cx="8" cy="8" rx="3" ry="6.5" fill="none" stroke="var(--red)" stroke-width="1"/><line x1="1.5" y1="8" x2="14.5" y2="8" stroke="var(--red)" stroke-width="1"/></svg>
      www.veldmarksupplies.com
    </li>
    <li class="contact-item">
      <svg class="icon" viewBox="0 0 16 16" aria-hidden="true"><path d="M8 15s5-5.5 5-9A5 5 0 0 0 3 6c0 3.5 5 9 5 9z" fill="var(--red)"/><circle cx="8" cy="6" r="1.8" fill="#fff"/></svg>
      417 N.Carrow Lane Suite 3, Midvale, Tx 79001
    </li>
  </ul>
  <div class="contact-rule"></div>

  <div class="back-brand">
    <span class="mark-square"></span>
    <span class="brand-name">Veldmark Supplies</span>
  </div>
</section>

</body>
</html>
```